Quiet Harbor, Weekly therapy lessons for the heart of a sister missionary

This is a weekly guided therapy book for female Mormon missionaries. They leave for their missions for 18 months and I am a psychotherapist that is creating a guided workbook to help them through mental health struggles on their mission. I need a good book cover, also preferably something for the spine and back as well. I would like something that gives a soft and safe feeling.

```html
<!DOCTYPE html>
<html lang="en">
<head>
<meta charset="utf-8">
<title>Quiet Harbor — Book Cover Wrap</title>
<link rel="stylesheet" href="https://fonts.googleapis.com/css2?family=Pinyon+Script&family=Libre+Baskerville&display=swap">
<style>
  :root {
    --paper: #e6e7e9;
    --teal: #7bc1c3;
    --teal-soft: #a9d6d7;
    --ink: #161616;
    --lamp: #2a2a2a;
    --lamp-glow: #f2d33a;
  }
  html, body {
    margin: 0;
    padding: 0;
    overflow: hidden;
    background: var(--paper);
  }
  .wrap {
    position: relative;
    width: 1200px;
    height: 864px;
    background: var(--paper);
    overflow: hidden;
  }
  .back-quote {
    position: absolute;
    left: 46px;
    top: 340px;
    width: 480px;
    margin: 0;
    font-family: "Libre Baskerville", Georgia, serif;
    font-size: 25px;
    line-height: 29px;
    text-align: center;
    color: var(--ink);
  }
  .lantern-art {
    position: absolute;
    left: 242px;
    top: 423px;
    width: 92px;
    height: 196px;
  }
  .spine-title {
    position: absolute;
    left: 598px;
    top: 298px;
    width: 0;
    height: 0;
  }
  .spine-title span {
    position: absolute;
    left: 0;
    top: 0;
    transform: rotate(90deg);
    transform-origin: 0 0;
    white-space: nowrap;
    font-family: "Pinyon Script", cursive;
    font-size: 44px;
    line-height: 44px;
    color: var(--teal);
    margin-left: 22px;
  }
  .front-title {
    position: absolute;
    left: 640px;
    top: 58px;
    margin: 0;
    font-family: "Pinyon Script", cursive;
    font-weight: 400;
    color: var(--teal);
    font-size: 120px;
    line-height: 1;
  }
  .front-title .word-one { display: block; }
  .front-title .word-two { display: block; margin-left: 200px; margin-top: -40px; }
  .front-subtitle {
    position: absolute;
    left: 668px;
    top: 290px;
    margin: 0;
    font-family: "Libre Baskerville", Georgia, serif;
    font-size: 28px;
    line-height: 34px;
    color: var(--ink);
  }
  .reader-art {
    position: absolute;
    left: 718px;
    top: 431px;
    width: 390px;
    height: 334px;
  }
</style>
</head>
<body>
<div class="wrap">
  <section class="back-cover">
    <p class="back-quote">“Let your light shine in the darkness<br>and your heart be filled with peace”</p>
    <svg class="lantern-art" viewBox="0 0 92 196" role="img" aria-label="Illustration of an old oil lantern with a glowing yellow glass">
      <defs>
        <radialGradient id="lanternGlow" cx="50%" cy="62%" r="55%">
          <stop offset="0%" stop-color="var(--lamp-glow)"/>
          <stop offset="45%" stop-color="var(--lamp-glow)" stop-opacity="0.85"/>
          <stop offset="100%" stop-color="var(--lamp)"/>
        </radialGradient>
      </defs>
      <rect x="0" y="0" width="92" height="196" rx="14" fill="url(#lanternGlow)"/>
    </svg>
  </section>

  <section class="spine">
    <div class="spine-title"><span>Quiet Harbor</span></div>
  </section>

  <section class="front-cover">
    <h1 class="front-title"><span class="word-one">Quiet</span><span class="word-two">Harbor</span></h1>
    <p class="front-subtitle">Weekly therapy lessons<br>for the heart of&nbsp; sister missionary</p>
    <svg class="reader-art" viewBox="0 0 390 334" role="img" aria-label="Illustration of a young woman in a patterned dress sitting on the ground reading a book">
      <defs>
        <linearGradient id="readerTone" x1="0" y1="0" x2="1" y2="1">
          <stop offset="0%" stop-color="var(--teal-soft)"/>
          <stop offset="100%" stop-color="var(--teal)"/>
        </linearGradient>
      </defs>
      <rect x="0" y="0" width="390" height="334" rx="22" fill="url(#readerTone)"/>
    </svg>
  </section>
</div>
</body>
</html>
```